White Paper and One-Page Advertisement for TELVORISH-QM

I need both documents to be better formatted and designed so they look professional, not something someone with mediocre word skills put together. They will go out to 1000s of industry professionals, and they need to look sharp. I need them to have my company's color palate logo, and branding on it similar to how it is now, but better. Please do not change any of the written content, but it can be arranged in any other format you think is better. Smart art and things i've already used can be omitted in favor of better designs. The developer is free to use their creativity. White paper should not be longer than the three pages unless necessary.

Target Market(s)

Life Sciences supply chain professionals

Colors
33b8a4
0592cd
9bcb3c
fbee3e
3277b5

Requirements
Must have
• Must be professional looking and not look like something done in word. Please use the color palate as seen on the documents.
Should not have
• Any changes to the written content.

```html
<!DOCTYPE html>
<html lang="en">
<head>
<meta charset="utf-8">
<title>Changing Pharma's Paradigm of Waste — White Paper Cover</title>
<link rel="stylesheet" href="https://fonts.googleapis.com/css2?family=Exo+2:wght@700;800&family=Open+Sans:wght@600;700&display=swap">
<style>
  :root {
    --stage: #2a2a2a;
    --green-deep: #1d5446;
    --green-mid: #2f6e5e;
    --green-soft: #4a8a79;
    --teal-light: #5f9c8b;
    --lime: #9bcb3c;
    --lime-text: #a8cf52;
    --white: #ffffff;
    --mist: #e9ecec;
    --photo-a: #dfe5e4;
    --photo-b: #b9d2cd;
  }
  * { margin: 0; padding: 0; box-sizing: border-box; }
  html, body {
    width: 1200px;
    height: 1134px;
    overflow: hidden;
    background: var(--stage);
  }
  .cover {
    position: absolute;
    left: 210px;
    top: 37px;
    width: 780px;
    height: 1060px;
    overflow: hidden;
    background: var(--mist);
    box-shadow: 0 10px 40px rgba(0,0,0,.45);
  }
  .cover__art {
    position: absolute;
    inset: 0;
    width: 100%;
    height: 100%;
  }
  .cover__heading {
    position: absolute;
    right: 60px;
    top: 96px;
    width: 620px;
    text-align: right;
  }
  .cover__title {
    font-family: "Exo 2", sans-serif;
    font-weight: 800;
    font-size: 47px;
    line-height: 1.12;
    letter-spacing: 0.5px;
    text-transform: uppercase;
    color: var(--lime-text);
  }
  .cover__subtitle {
    margin-top: 34px;
    margin-left: auto;
    width: 470px;
    font-family: "Open Sans", sans-serif;
    font-weight: 700;
    font-size: 21px;
    line-height: 1.32;
    color: var(--white);
  }
  .cover__byline {
    margin-top: 44px;
    font-family: "Open Sans", sans-serif;
    font-weight: 700;
    font-size: 22px;
    line-height: 1.4;
    color: var(--white);
  }
  .brand {
    position: absolute;
    left: 46px;
    top: 560px;
    display: flex;
    align-items: center;
    gap: 10px;
  }
  .brand__dot {
    width: 22px;
    height: 22px;
    border-radius: 50%;
    background: var(--lime);
  }
  .brand__name {
    font-family: "Exo 2", sans-serif;
    font-weight: 800;
    font-size: 22px;
    letter-spacing: 0.5px;
    color: var(--green-mid);
  }
</style>
</head>
<body>
  <main class="cover">
    <svg class="cover__art" viewBox="0 0 780 1060" aria-hidden="false">
      <defs>
        <linearGradient id="greenFill" x1="0" y1="0" x2="1" y2="1">
          <stop offset="0" stop-color="#1a4d40"/>
          <stop offset="0.6" stop-color="#2a6656"/>
          <stop offset="1" stop-color="#3a7b6a"/>
        </linearGradient>
        <linearGradient id="photoFill" x1="0" y1="0" x2="1" y2="1">
          <stop offset="0" stop-color="#eef1f0"/>
          <stop offset="0.5" stop-color="#d6e4e1"/>
          <stop offset="1" stop-color="#a9cbc4"/>
        </linearGradient>
        <clipPath id="photoClip">
          <path d="M0,360 C260,470 520,560 780,610 V1060 H0 Z"/>
        </clipPath>
      </defs>

      <!-- upper green field -->
      <path d="M0,0 H780 V640 C560,580 300,470 0,340 Z" fill="url(#greenFill)"/>
      <!-- lighter left sweep -->
      <path d="M0,0 H260 C130,110 40,240 0,430 Z" fill="var(--teal-light)" opacity="0.55"/>
      <!-- lime accent under the green field -->
      <path d="M0,352 C220,450 420,530 640,590" fill="none" stroke="var(--lime)" stroke-width="14"/>
      <!-- white sweep -->
      <path d="M0,372 C240,470 470,560 780,625" fill="none" stroke="var(--white)" stroke-width="18" opacity="0.9"/>

      <!-- photo area -->
      <g clip-path="url(#photoClip)" role="img" aria-label="Photo: smiling nurse with stethoscope comforting an elderly woman wrapped in a white blanket">
        <rect x="150" y="560" width="630" height="440" fill="url(#photoFill)"/>
      </g>

      <!-- lower band -->
      <path d="M0,998 C280,960 540,905 780,858" fill="none" stroke="var(--white)" stroke-width="10"/>
      <path d="M0,1012 C280,974 540,920 780,874" fill="none" stroke="var(--lime)" stroke-width="14"/>
      <path d="M0,1022 C280,985 540,932 780,886 V1060 H0 Z" fill="url(#greenFill)"/>
    </svg>

    <header class="cover__heading">
      <h1 class="cover__title">Changing Pharma’s<br>Paradigm of Waste</h1>
      <p class="cover__subtitle">How Pharma’s Demand Volatility Could Be Costing You Millions in Material Write-downs &amp; Procurement</p>
      <p class="cover__byline">Dale Marrow<br>August 2018</p>
    </header>

    <div class="brand">
      <span class="brand__dot"></span>
      <span class="brand__name">TELVORISH-QM</span>
    </div>
  </main>
</body>
</html>
```